Request for Business Card Design

Hi. My name is Marlene, I am looking for a new business card design for my company, Quarrow Signal Instruments, LLC. I really like the design you did for Tarsel Venture and was hoping you could do something similar using our full logo and our mark. I am also open to any raised texture design using our mark. I have attached our full logo, which would need to be somewhere on the card, as well as the mark in both outline and full form, as well as our brand colors / guide. The card does not have to be white, as long as our logo and mark appear. I actually like darker colored business cards more, but am open to all options. If you are interested in working with me, please let me know. We would also take the business card design into letterhead design if you can do that.

```html
<!DOCTYPE html>
<html lang="en">
<head>
<meta charset="utf-8">
<title>Quarrow Signal Instruments – Business Card</title>
<link href="https://fonts.googleapis.com/css2?family=Roboto:wght@400;500&display=swap" rel="stylesheet">
<style>
  :root {
    --backdrop: #ababab;
    --card-light: #ffffff;
    --card-dark: #404042;
    --ink: #3d3d3f;
    --ink-soft: #1f1f1f;
    --brand-blue: #129bc5;
    --divider: #b9b9b9;
    --on-dark: #ffffff;
  }
  * { margin: 0; padding: 0; box-sizing: border-box; }
  html, body {
    width: 1093px; height: 1200px; overflow: hidden;
    background: var(--backdrop);
    font-family: "Roboto", Arial, sans-serif;
  }
  .canvas { position: relative; width: 1093px; height: 1200px; }
  .card {
    position: absolute; left: 264px; width: 580px; height: 356px;
    border-radius: 24px; overflow: hidden;
  }
  .card--front { top: 226px; background: var(--card-light); }
  .card--back { top: 621px; background: var(--card-dark); }

  .brand { position: absolute; display: flex; align-items: center; }
  .brand__dot { border-radius: 50%; background: var(--brand-blue); flex: none; }
  .brand__name {
    font-weight: 500; letter-spacing: 0.06em; text-transform: uppercase; line-height: 1.15;
  }
  .card--front .brand { left: 30px; top: 153px; gap: 14px; }
  .card--front .brand__dot { width: 44px; height: 44px; }
  .card--front .brand__name { color: var(--ink); font-size: 17px; }
  .card--back .brand { left: 110px; top: 136px; gap: 22px; }
  .card--back .brand__dot { width: 70px; height: 70px; }
  .card--back .brand__name { color: var(--on-dark); font-size: 27px; }

  .divider {
    position: absolute; left: 292px; top: 75px; width: 1px; height: 208px;
    background: linear-gradient(transparent, var(--divider) 15%, var(--divider) 85%, transparent);
  }
  .details { position: absolute; left: 312px; top: 90px; color: var(--ink-soft); }
  .details__name { font-size: 23px; font-weight: 500; color: var(--ink); line-height: 1; }
  .details__role { font-size: 17.5px; color: var(--brand-blue); line-height: 1.1; margin-top: 2px; }
  .contact { list-style: none; margin-top: 14px; }
  .contact li {
    display: flex; align-items: center; gap: 7px;
    font-size: 17px; line-height: 21px;
  }
  .contact svg { width: 15px; height: 15px; flex: none; }
  .accent { color: var(--brand-blue); }
  .address { font-size: 17px; line-height: 21px; margin-top: 13px; }
</style>
</head>
<body>
<main class="canvas">
  <section class="card card--front" aria-label="Card front">
    <div class="brand">
      <span class="brand__dot"></span>
      <span class="brand__name">Quarrow<br>Signal Instruments</span>
    </div>
    <div class="divider"></div>
    <div class="details">
      <p class="details__name">DORIAN PELL</p>
      <p class="details__role">Managing Director</p>
      <ul class="contact">
        <li>
          <svg viewBox="0 0 16 16" fill="none" stroke="#129bc5" stroke-width="1.6"><path d="M4 2l2 3-1.5 1.5a8 8 0 0 0 5 5L11 10l3 2-1 2.5C7 15 1 9 1.5 3z"/><path d="M9 2a5 5 0 0 1 5 5M9 4.5A2.5 2.5 0 0 1 11.5 7"/></svg>
          044-987 210 654
        </li>
        <li>
          <svg viewBox="0 0 16 16"><rect x="0.5" y="3" width="15" height="10" fill="#129bc5"/><path d="M0.5 3l7.5 6 7.5-6M0.5 13l5.5-5M15.5 13l-5.5-5" stroke="#fff" stroke-width="1" fill="none"/></svg>
          info@quarrowsignal.com
        </li>
        <li>
          <svg viewBox="0 0 16 16" fill="none" stroke="#129bc5" stroke-width="1.3"><circle cx="8" cy="8" r="7"/><ellipse cx="8" cy="8" rx="3" ry="7"/><path d="M1 8h14M2 4.5h12M2 11.5h12"/></svg>
          <span>www.<span class="accent">quarrowsignal</span>.com</span>
        </li>
      </ul>
      <p class="address">88, Linden Works Road<br>40718, Halvern</p>
    </div>
  </section>

  <section class="card card--back" aria-label="Card back">
    <div class="brand">
      <span class="brand__dot"></span>
      <span class="brand__name">Quarrow<br>Signal Instruments</span>
    </div>
  </section>
</main>
</body>
</html>
```